New Business Card Design Project

We require a business card design for Vexalund, a newly established Indian company.
Our focus is on the development, manufacturing, and export of a diverse array of pharmaceutical products on a global scale. The card should convey a professional appearance, as our primary markets are in Africa, China, and Southeast Asian nations.
We envision a two-sided business card, with the reverse side dedicated to a logo set against a solid color or an elegantly designed pattern. The corners should be rounded. We would appreciate seeing both horizontal and vertical design options. We trust the designer to utilize their expertise in creating this design.

The content for the business card is included in the attached Word file.

Target Market(s)

Our primary markets are in Africa, China, and Southeast Asian, Latin America, Maldives, Sri Lanka

Industry/Entity Type

Pharmaceutical Manufacturing and Export

Contact Information for Business Card

Colors

Designer to choose colors to be used in the design.

Requirements
Must have
• The reverse side of the business card features solely the logo along with the tagline, "Care in Every Dose."
Should not have
• The logo should not exceed two instances, encompassing both the front and back sides of the card.

```html
<!DOCTYPE html>
<html lang="en">
<head>
<meta charset="utf-8">
<title>Vexalund Business Card</title>
<link rel="stylesheet" href="https://fonts.googleapis.com/css2?family=Poppins:wght@400;600;700&family=Open+Sans:wght@400;600&display=swap">
<style>
  :root {
    --stage: #222223;
    --card: #1e1e21;
    --edge: #2aa5e0;
    --brand-blue: #2ba6df;
    --brand-coral: #f0634f;
    --ink: #f2f2f2;
  }
  * { box-sizing: border-box; margin: 0; padding: 0; }
  html, body { width: 1200px; height: 711px; overflow: hidden; background: var(--stage); }
  .stage {
    position: relative; width: 1200px; height: 711px;
    display: flex; align-items: center; justify-content: center; gap: 40px;
  }
  .card {
    position: relative; width: 540px; height: 310px;
    background: var(--card); border-radius: 20px;
    border-bottom: 4px solid var(--edge);
    box-shadow: 0 18px 30px rgba(0,0,0,.55);
    overflow: hidden;
  }
  /* back side */
  .card--back { display: flex; flex-direction: column; align-items: center; justify-content: center; }
  .wordmark {
    display: flex; align-items: center; gap: 12px;
    font-family: "Poppins", sans-serif; font-weight: 700; color: var(--brand-blue);
    white-space: nowrap;
  }
  .wordmark__dot { border-radius: 50%; background: var(--brand-coral); flex: none; }
  .card--back .wordmark { font-size: 58px; line-height: 1; }
  .card--back .wordmark__dot { width: 28px; height: 28px; }
  .tagline {
    margin-top: 16px; font-family: "Poppins", sans-serif; font-size: 14px;
    color: var(--ink); letter-spacing: .5px;
  }
  /* front side */
  .identity { position: absolute; left: 0; top: 40px; display: flex; }
  .identity__bar { width: 24px; height: 64px; background: var(--brand-blue); }
  .identity__text { padding-left: 14px; padding-top: 2px; }
  .identity__name { font-family: "Poppins", sans-serif; font-size: 25px; line-height: 1.1; white-space: nowrap; }
  .identity__first { color: var(--brand-blue); font-weight: 700; }
  .identity__rest { color: var(--brand-coral); font-weight: 400; }
  .identity__role { font-family: "Open Sans", sans-serif; font-size: 14px; color: var(--ink); margin-top: 4px; }
  .card--front .wordmark { position: absolute; right: 30px; top: 40px; font-size: 40px; line-height: 1; gap: 9px; }
  .card--front .wordmark__dot { width: 18px; height: 18px; }
  .contacts {
    position: absolute; right: 28px; top: 150px; list-style: none;
    font-family: "Open Sans", sans-serif; font-size: 14px; color: var(--ink);
  }
  .contacts li { display: flex; align-items: center; justify-content: flex-end; gap: 10px; height: 25px; white-space: nowrap; }
  .contacts svg { width: 15px; height: 15px; flex: none; }
  .address {
    position: absolute; left: 40px; bottom: 24px;
    font-family: "Open Sans", sans-serif; font-size: 14px; line-height: 1.5; color: var(--ink);
  }
</style>
</head>
<body>
<main class="stage">
  <section class="card card--back" aria-label="Card back">
    <div class="wordmark"><span class="wordmark__dot"></span><span>Vexalund</span></div>
    <p class="tagline">Care in Every Dose.</p>
  </section>

  <section class="card card--front" aria-label="Card front">
    <div class="identity">
      <span class="identity__bar"></span>
      <div class="identity__text">
        <p class="identity__name"><span class="identity__first">Ravi</span> <span class="identity__rest">K. Solanki</span></p>
        <p class="identity__role">CEO</p>
      </div>
    </div>

    <div class="wordmark"><span class="wordmark__dot"></span><span>Vexalund</span></div>

    <ul class="contacts">
      <li>+91 98765 43210
        <svg viewBox="0 0 16 16"><rect x="4" y="1.5" width="8" height="13" rx="1.5" fill="none" stroke="var(--brand-coral)" stroke-width="1.6"/></svg>
      </li>
      <li>www.vexalund.com
        <svg viewBox="0 0 16 16"><circle cx="8" cy="8" r="6.5" fill="var(--brand-blue)"/><path d="M1.5 8h13M8 1.5c3 3.5 3 9.5 0 13M8 1.5c-3 3.5-3 9.5 0 13" fill="none" stroke="var(--card)" stroke-width="1"/></svg>
      </li>
      <li>rsolanki@vexalund.com
        <svg viewBox="0 0 16 16"><rect x="1.5" y="4" width="13" height="9" rx="1" fill="var(--brand-coral)"/><path d="M1.5 4.5 8 9.5l6.5-5" fill="none" stroke="var(--card)" stroke-width="1.2"/></svg>
      </li>
    </ul>

    <p class="address">12, Lotus Colony,<br>Ambergaon, 440210, India</p>
  </section>
</main>
</body>
</html>
```